Laser Tattoo Removal Business Cards

We are looking for a professional business card design for a laser tattoo removal business. Ideally looking for a black business card design. The name of the business is Brightline Tattoo Removal. We place our cards at local tattoo shops so we ideally are looking for something trendy/edgy to draw both male and female clientele in.

Target Market(s)

Male/Female ages 18-60

Contact Information for Business Card

black background ideally.. hoping to stay within greys, whites and black

Font styles to use
Serif
Sans Serif

Colors
121212
a9a9a9
5c5c5c
f5f5f5
ffffff
7f7f7f
606060
848484
9d9d9d

Requirements
Must have
• Employee Info:
• Melissa Thornbury
• Chief Executive Offer
• m: 919.537.2846
• w: 919.362.4178
• f: 919.685.3907
• mthornbury@brightlinetattooremoval.example
• Address:
• 4615 Oakmere Pkwy, Suite 210
• Raleigh, NC 27654
• Website:
• www.brightlinetattooremoval.example
Nice to have
• Myabe business name on back or logo on back and employee info on the front

```html
<!DOCTYPE html>
<html lang="en">
<head>
<meta charset="utf-8">
<title>Brightline Tattoo Removal – Business Card</title>
<link rel="stylesheet" href="https://fonts.googleapis.com/css2?family=Lato:wght@400;700&family=Arimo:wght@400&display=swap">
<style>
  :root {
    --backdrop: #9d9d9d;
    --card: #121212;
    --text-strong: #d4d4d4;
    --text: #f5f5f5;
    --text-soft: #a9a9a9;
    --rule: #7f7f7f;
    --icon: #a9a9a9;
  }
  * { margin: 0; padding: 0; box-sizing: border-box; }
  html, body { width: 1200px; height: 1200px; overflow: hidden; }
  body { background: var(--backdrop); position: relative; font-family: "Arimo", Arial, sans-serif; }

  .card {
    position: absolute;
    top: 310px;
    width: 364px;
    height: 594px;
    background: var(--card);
    color: var(--text);
    text-align: center;
  }
  .card--front { left: 234px; }
  .card--back { left: 633px; }

  .holder { position: absolute; top: 404px; left: 0; right: 0; }
  .card--front .holder { top: 94px; }
  .holder__name {
    font-family: "Lato", sans-serif;
    font-weight: 700;
    font-size: 25px;
    letter-spacing: 0.2px;
    color: var(--text-strong);
    line-height: 30px;
  }
  .holder__title { font-size: 17px; color: var(--text-soft); line-height: 22px; }

  .divider {
    position: absolute;
    left: 84px;
    width: 196px;
    height: 36px;
  }
  .divider::before, .divider::after {
    content: "";
    position: absolute;
    top: 17px;
    width: 80px;
    height: 1px;
    background: var(--rule);
  }
  .divider::before { left: 0; }
  .divider::after { right: 0; }
  .divider svg { position: absolute; left: 80px; top: 0; width: 36px; height: 36px; }

  .divider--phone { top: 195px; }
  .divider--web { top: 335px; }
  .divider--place { top: 444px; }

  .info {
    position: absolute;
    left: 0; right: 0;
    font-size: 17px;
    line-height: 23px;
    color: var(--text);
  }
  .info--phones { top: 244px; }
  .info--web { top: 383px; font-size: 15px; line-height: 22px; }
  .info--place { top: 494px; line-height: 22px; }

  .brand {
    position: absolute;
    top: 262px;
    left: 0; right: 0;
    font-family: "Lato", sans-serif;
    font-weight: 700;
    font-size: 30px;
    line-height: 38px;
    letter-spacing: 3px;
    text-transform: uppercase;
    color: var(--text);
  }
  .brand__dot {
    display: block;
    width: 14px; height: 14px;
    margin: 0 auto 14px;
    border-radius: 50%;
    background: var(--text);
  }
  .card__url {
    position: absolute;
    top: 512px;
    left: 0; right: 0;
    font-family: "Lato", sans-serif;
    font-size: 15px;
    letter-spacing: 0.8px;
    color: var(--text);
  }
</style>
</head>
<body>

  <section class="card card--front" aria-label="Business card front">
    <div class="holder">
      <p class="holder__name">MELISSA THORNBURY</p>
      <p class="holder__title">Chief Executive Officer</p>
    </div>

    <div class="divider divider--phone">
      <svg viewBox="0 0 36 36" aria-hidden="true">
        <circle cx="18" cy="18" r="16" fill="none" stroke="var(--icon)" stroke-width="2.5"/>
        <path d="M13.5 10.5c-1.5 1-2 2.6-1.2 4.6 1.6 4 4.6 7 8.6 8.6 2 .8 3.6.3 4.6-1.2l-2.6-2.4-2 1.2c-2-1-3.8-2.8-4.8-4.8l1.2-2z" fill="none" stroke="var(--icon)" stroke-width="1.8" stroke-linejoin="round"/>
      </svg>
    </div>
    <p class="info info--phones">919.537.2846<br>919.362.4178<br>919.685.3907</p>

    <div class="divider divider--web">
      <svg viewBox="0 0 36 36" aria-hidden="true">
        <circle cx="18" cy="18" r="16" fill="none" stroke="var(--icon)" stroke-width="2.5"/>
        <circle cx="18" cy="18" r="9" fill="var(--icon)"/>
        <path d="M13 13c2 1 3 3 2 5s1 3 3 3M20 10c0 2 2 3 4 3M22 26c0-2 1-3 3-3" fill="none" stroke="var(--card)" stroke-width="1.6"/>
      </svg>
    </div>
    <p class="info info--web">mthornbury@brightlinetattooremoval.example<br>www.brightlinetattooremoval.example</p>

    <div class="divider divider--place">
      <svg viewBox="0 0 36 36" aria-hidden="true">
        <circle cx="18" cy="18" r="16" fill="none" stroke="var(--icon)" stroke-width="2.5"/>
        <path d="M18 27c-4-5-6-8-6-11a6 6 0 0 1 12 0c0 3-2 6-6 11z" fill="none" stroke="var(--icon)" stroke-width="1.8" stroke-linejoin="round"/>
        <circle cx="18" cy="16" r="2.2" fill="var(--icon)"/>
      </svg>
    </div>
    <p class="info info--place">4615 Oakmere Pkwy, Suite 210<br>Raleigh, NC 27654</p>
  </section>

  <section class="card card--back" aria-label="Business card back">
    <p class="brand"><span class="brand__dot"></span>Brightline<br>Tattoo Removal</p>
    <p class="card__url">www.brightlinetattooremoval.example</p>
  </section>

</body>
</html>
```